Mortgage Company ready to make a statement!

We have a basic logo that I am fairly happy with ... but it could use a little bit of tweaking before we order the sign for our building. We also want some knock-your-socks-off business cards.
Problem: Inside of our Mortgage Office (Bright Fern Mortgage Group), we are going to have a coffee lounge (Sunbrew Cafe) for Realtors to use instead of the local Cuppington to meet with homebuyers. The office and coffee lounge are in an industrial building and is decorated with cozy overstuffed chairs, a hodge podge of interesting lamps and furniture, and goal is to make it as inviting as possible. However, we are a financial institution... so we need to keep it pretty clean as well.
One of my favorite marketing ideas is to cut a house key for everyone who buys a home using us with a key that matches our logo. There's only one key shape that works really well, so that needs to match the logo in order for the idea to work. I'll attach an image of the key blank.... although the way the key hole cut out looks terrible, so I was thinking of having them just do a thin outline instead.
Would like a similar, matching logo for the Sunbrew Cafe... but possibly something that would be a little less formal and would be cute on a coffee mug- nothing stuffy.
AND, we're opening a home inspection company as well, and we would like that logo and branding to match. The home inspection company is "Bright Fern Home Inspections"
We were thinking that for the home inspection company , we could use a magnifying glass shape inside of the house shape for the logo, use a keyhole shape inside of the same house for the mortgage company, and use a coffee cup inside of the house shape for Sunbrew Cafe.
Just getting stuck and need to help. I designed the attached logo myself, and that is what we are currently using. Designers at local printing companies have failed to impress us.
The mortgage industry has a lot of numbers and logos, etc that they require us to put on our business cards... so it's hard to keep them looking clean.
HELP! HELP! :)

```html
<!DOCTYPE html>
<html lang="en">
<head>
<meta charset="utf-8">
<title>Bright Fern Mortgage Group — Business Cards</title>
<link href="https://fonts.googleapis.com/css2?family=Marcellus&family=Montserrat:wght@400;600&display=swap" rel="stylesheet">
<style>
  :root {
    --backdrop: #2b2b2d;
    --card: #1c1c1c;
    --ink: #f4f4f4;
    --ink-soft: #e2e2e2;
  }
  * { box-sizing: border-box; margin: 0; padding: 0; }
  html, body { width: 1200px; height: 900px; overflow: hidden; }
  body {
    background: var(--backdrop);
    position: relative;
    font-family: "Montserrat", sans-serif;
    color: var(--ink);
  }
  .card {
    position: absolute;
    left: 280px;
    width: 640px;
    height: 366px;
    background: var(--card);
    box-shadow: 0 14px 30px rgba(0,0,0,0.45);
    overflow: hidden;
  }
  .card-front { top: 62px; }
  .card-back { top: 470px; }

  .brand {
    display: flex;
    align-items: center;
    gap: 18px;
    font-family: "Marcellus", serif;
    color: var(--ink);
    white-space: nowrap;
  }
  .brand-dot {
    width: 22px; height: 22px;
    border-radius: 50%;
    background: var(--ink);
    flex: none;
  }
  .brand-name {
    font-size: 40px;
    line-height: 1.08;
    letter-spacing: 0.5px;
  }
  .card-front .brand {
    position: absolute;
    left: 50%; top: 50%;
    transform: translate(-50%, -50%);
  }

  .card-back .brand {
    position: absolute;
    left: 40px; top: 128px;
  }
  .card-back .brand-name { font-size: 32px; }

  .divider {
    position: absolute;
    left: 372px; top: 74px;
    width: 2px; height: 222px;
    background: var(--ink);
  }
  .contact {
    position: absolute;
    left: 396px; top: 84px;
    width: 224px;
    white-space: nowrap;
  }
  .person-name {
    font-family: "Marcellus", serif;
    font-size: 24px;
    letter-spacing: 2px;
    text-transform: uppercase;
  }
  .person-title {
    font-weight: 600;
    font-size: 15px;
    letter-spacing: 1px;
    margin-top: 2px;
  }
  .address {
    margin-top: 18px;
    font-size: 14px;
    line-height: 1.35;
    letter-spacing: 1.5px;
    color: var(--ink-soft);
  }
  .contact-list { list-style: none; margin-top: 14px; }
  .contact-list li {
    display: flex;
    align-items: center;
    gap: 12px;
    font-size: 14.5px;
    letter-spacing: 1.4px;
    line-height: 1.75;
  }
  .contact-list svg { width: 14px; height: 14px; flex: none; fill: var(--ink); }
</style>
</head>
<body>

  <section class="card card-front">
    <div class="brand">
      <span class="brand-dot"></span>
      <span class="brand-name">Bright Fern<br>Mortgage Group</span>
    </div>
  </section>

  <section class="card card-back">
    <div class="brand">
      <span class="brand-dot"></span>
      <span class="brand-name">Bright Fern<br>Mortgage Group</span>
    </div>

    <div class="divider"></div>

    <div class="contact">
      <p class="person-name">Dana Hale</p>
      <p class="person-title">CEO</p>
      <p class="address">Harbour Point<br>Riverton Eastvale</p>
      <ul class="contact-list">
        <li>
          <svg viewBox="0 0 14 14" aria-hidden="true"><path d="M4 0h6a1 1 0 0 1 1 1v12a1 1 0 0 1-1 1H4a1 1 0 0 1-1-1V1a1 1 0 0 1 1-1zm0.6 1.6v9.6h4.8V1.6zM7 11.8a0.7 0.7 0 1 0 0 1.4a0.7 0.7 0 0 0 0-1.4z"/></svg>
          000-555-0142
        </li>
        <li>
          <svg viewBox="0 0 14 14" aria-hidden="true"><path d="M3.5 0h7v4h-7zM1 5h12a1 1 0 0 1 1 1v5h-2.5v3h-9v-3H0V6a1 1 0 0 1 1-1zm3.5 4.5V12.5h5V9.5z"/></svg>
          000-555-0142
        </li>
        <li>
          <svg viewBox="0 0 14 14" aria-hidden="true"><path d="M0 3h14v1L7 8.2L0 4zM0 5.4l7 4.2l7-4.2V12H0z"/></svg>
          dana@brightfern.com
        </li>
      </ul>
    </div>
  </section>

</body>
</html>
```